Fenwick Ridge Accounting - New client package

I need a stationary package (presentation folder cover, welcome letter template/design, sample financial report template/design, business card and new logo) for my accounting business. I would like to see designs that use the color blue. Financial icons can be included in the design. The final design should be clean and communicate professionalism and the use of modern; user-friendly technology. Attached postcard files should help with overall design concept.

```html
<!DOCTYPE html>
<html lang="en">
<head>
<meta charset="utf-8">
<title>Fenwick Ridge Accounting – Presentation Folder</title>
<link href="https://fonts.googleapis.com/css2?family=Montserrat:wght@300;400;600&display=swap" rel="stylesheet">
<style>
  :root {
    --navy: #024d8a;
    --sky: #1693c9;
    --paper: #ffffff;
    --backdrop: #dcdcde;
    --ink-light: #e8f2fa;
  }
  * { margin: 0; padding: 0; box-sizing: border-box; }
  html, body { width: 1200px; height: 854px; overflow: hidden; }
  body {
    background: var(--backdrop);
    font-family: "Montserrat", sans-serif;
    position: relative;
  }
  .folder-spread {
    position: absolute;
    left: 160px;
    top: 127px;
    width: 880px;
    height: 600px;
    background: var(--paper);
    box-shadow: 0 10px 30px rgba(0,0,0,0.18);
  }
  .folder-shapes { position: absolute; inset: 0; }
  .spine {
    position: absolute;
    left: 440px; top: 0;
    width: 1px; height: 600px;
    background: rgba(0,0,0,0.08);
  }

  /* Back cover */
  .back-signature {
    position: absolute;
    left: 44px; top: 538px;
    display: flex; align-items: center; gap: 8px;
    color: var(--paper);
    font-size: 9px; font-weight: 400;
    letter-spacing: 0.12em; text-transform: uppercase;
  }
  .back-signature .mark-square {
    width: 12px; height: 12px;
    background: var(--sky);
  }
  .contact-address {
    position: absolute;
    left: 226px; top: 500px;
    color: var(--ink-light);
    font-size: 7px; line-height: 1.5;
  }
  .contact-lines {
    position: absolute;
    left: 316px; top: 484px;
    list-style: none;
    color: var(--ink-light);
    font-size: 7px; line-height: 1.5;
  }
  .contact-lines li { display: flex; align-items: center; gap: 5px; }
  .contact-lines svg { width: 7px; height: 7px; fill: none; stroke: var(--sky); stroke-width: 1.6; }

  /* Front cover */
  .front-name {
    position: absolute;
    left: 440px; top: 78px;
    width: 440px;
    display: flex; justify-content: center; align-items: center; gap: 12px;
    color: var(--navy);
    font-size: 22px; font-weight: 600;
    letter-spacing: 0.02em;
  }
  .front-name .mark-square {
    width: 22px; height: 22px;
    background: var(--sky);
  }
  .front-title {
    position: absolute;
    left: 556px; top: 410px;
    color: var(--paper);
    font-size: 25px; font-weight: 300;
    line-height: 1.12;
    letter-spacing: 0.08em;
    text-transform: uppercase;
  }
</style>
</head>
<body>
  <main class="folder-spread">
    <svg class="folder-shapes" viewBox="0 0 880 600" width="880" height="600" aria-hidden="true">
      <!-- back cover -->
      <polygon class="back-accent" points="0,0 270,0 0,265" fill="var(--sky)"/>
      <polygon class="back-field" points="0,290 165,125 440,200 440,600 0,600" fill="var(--navy)"/>
      <!-- front cover -->
      <polygon class="front-field" points="440,200 880,565 880,600 440,600" fill="var(--navy)"/>
      <polygon class="front-accent" points="880,280 648,395 880,545" fill="var(--sky)"/>
    </svg>
    <div class="spine"></div>

    <section class="back-cover">
      <address class="contact-address">
        Level 12, Harbour House<br>88 Kent Lane<br>Sydney
      </address>
      <ul class="contact-lines">
        <li><svg viewBox="0 0 10 10"><path d="M2 1 L4 1 L4.5 3 L3.5 4 Q4.5 6 6 6.5 L7 5.5 L9 6 L9 8 Q5 9 1 3 Z"/></svg>305-555-0148</li>
        <li><svg viewBox="0 0 10 10"><rect x="1" y="2" width="8" height="6"/><path d="M1 2 L5 5.5 L9 2"/></svg>info@fenwickridge.com</li>
        <li><svg viewBox="0 0 10 10"><circle cx="5" cy="5" r="4"/><path d="M1 5 H9 M5 1 Q2 5 5 9 Q8 5 5 1"/></svg>www.fenwickridge.com</li>
      </ul>
      <div class="back-signature"><span class="mark-square"></span>Fenwick Ridge Accounting</div>
    </section>

    <section class="front-cover">
      <div class="front-name"><span class="mark-square"></span>Fenwick Ridge Accounting</div>
      <h1 class="front-title">Fenwick<br>Ridge<br>Accounting</h1>
    </section>
  </main>
</body>
</html>
```